Business Cards for IT Consulting Company (Managed Service Provider)

I am looking to have some business cards printed and would like some designs. We are an IT Consulting company based in Vancouver BC. I would like a nice clean and modern look to the cards. I have uploaded all the versions of my logo so parts can be used as needed. Here is a snippit from our website homepage:

Quillbrook Networks Ltd. is an IT Solutions Partner located in Vancouver BC, Canada. We offer IT solutions and support to customers in the greater Vancouver Area. With expertise in Microsoft platforms, as well as Linux and Mac OSX and over 12 years experience in the IT industry, Quillbrook Networks is dedicated to offering our clients top quality service and products. We take pride in the solutions we offer our customers. The greatest compliment a client can give us is to recommend our services.

Quillbrook Networks Ltd. offers a wide range of IT services from onsite service to remote support and managed service solutions. This allows clients to choose the support path that best suits their company’s needs. Supporting many different sized companies from small to enterprise level over the past 12 years Quillbrook Networks has the experience and expertise needed to ensure things run smoothly. Allowing our clients to focus on doing business.

Revolutionizing the way IT services are delivered.

Quillbrook Networks is dedicated to providing our clients with IT solutions that work and grow with them for years to come. This philosophy helps save money in the long run instead of replacing equipment constantly. Far too often IT solutions are not well thought out and while possibly solving the problem at hand, require replacement due to growth or quality within a very short time frame. Quillbrook Networks takes pride in providing solutions that will last and be able to accommodate growth without the need for replacement.

Industry/Entity Type

Information Technology

Contact Information for Business Card

Quillbrook Networks Ltd.
(Employee Name)
Eml: (Employees Email Address)
Web: quillbrook.me
Ph: 604-555-0148

Font styles to use
Serif
Sans Serif

Requirements
Must have
• The Company logo and company colors.
Nice to have
• - Our tag line: "Revolutionizing IT Services" or "Revolutionizing the way IT services are delivered."
• - Also I really like the idea of nature and technology together blending which is sort of where my logo came from so integrating that somehow onto the business cards would be great.

```html
<!DOCTYPE html>
<html lang="en">
<head>
<meta charset="utf-8">
<title>Quillbrook Networks Ltd. – Business Cards</title>
<link rel="stylesheet" href="https://fonts.googleapis.com/css2?family=Montserrat:wght@500;600&family=Roboto:ital,wght@0,400;0,500;1,400&display=swap">
<style>
  :root {
    --backdrop: #a9a7a8;
    --card-dark: #1f1f1f;
    --card-light: #f2f2f2;
    --brand-blue: #1a8fd4;
    --brand-gray: #6b6c6e;
    --text-light: #ffffff;
    --text-soft: #e6f1fa;
  }
  * { margin: 0; padding: 0; box-sizing: border-box; }
  html, body {
    width: 1200px; height: 1200px; overflow: hidden;
    background: var(--backdrop);
  }
  .canvas { position: relative; width: 1200px; height: 1200px; }
  .card {
    position: absolute; width: 712px; height: 420px; overflow: hidden;
  }
  /* Front */
  .card--front { left: 238px; top: 117px; background: var(--card-dark); }
  .brand-lockup {
    position: absolute; left: 110px; top: 140px;
    display: flex; align-items: center; gap: 24px;
  }
  .brand-lockup__square {
    width: 62px; height: 62px; background: var(--brand-blue);
  }
  .brand-lockup__name {
    font-family: "Montserrat", sans-serif; font-weight: 500;
    color: var(--brand-blue); line-height: 1;
  }
  .brand-lockup__name .line-main { display: block; font-size: 66px; letter-spacing: -1px; }
  .brand-lockup__name .line-sub { display: block; font-size: 25px; letter-spacing: 1px; margin-top: 6px; }
  .tagline {
    position: absolute; left: 0; right: 0; top: 377px;
    display: flex; justify-content: center; align-items: center; gap: 16px;
    font-family: "Montserrat", sans-serif; font-weight: 500; font-size: 18px;
    color: var(--text-light);
  }
  .tagline__rule { width: 110px; height: 3px; background: var(--brand-blue); }

  /* Back */
  .card--back { left: 230px; top: 643px; background: var(--card-light); }
  .card__shapes { position: absolute; inset: 0; }
  .brand-vertical {
    position: absolute; left: 150px; top: 210px;
    transform: translate(-50%, -50%) rotate(-90deg);
    display: flex; align-items: center; gap: 18px;
    white-space: nowrap;
  }
  .brand-vertical__square { width: 44px; height: 44px; background: var(--brand-blue); }
  .brand-vertical__name {
    font-family: "Montserrat", sans-serif; font-weight: 500;
    color: var(--brand-blue); line-height: 1;
  }
  .brand-vertical__name .line-main { display: block; font-size: 46px; letter-spacing: -1px; }
  .brand-vertical__name .line-sub { display: block; font-size: 18px; letter-spacing: 1px; margin-top: 4px; }

  .contact-block {
    position: absolute; left: 392px; top: 128px;
    font-family: "Roboto", sans-serif; color: var(--text-light);
  }
  .contact-block__name { font-size: 25px; font-weight: 500; }
  .contact-block__role { font-size: 16px; font-style: italic; color: var(--text-soft); margin-top: 6px; }
  .contact-list { list-style: none; margin-top: 30px; }
  .contact-list li {
    display: flex; align-items: center; gap: 18px;
    font-size: 18px; height: 28px;
  }
  .contact-list svg { width: 18px; height: 18px; fill: var(--text-light); }
</style>
</head>
<body>
<main class="canvas">

  <section class="card card--front" aria-label="Business card front">
    <div class="brand-lockup">
      <span class="brand-lockup__square"></span>
      <p class="brand-lockup__name">
        <span class="line-main">Quillbrook</span>
        <span class="line-sub">NETWORKS LTD.</span>
      </p>
    </div>
    <p class="tagline">
      <span class="tagline__rule"></span>
      Revolutionizing IT Services
      <span class="tagline__rule"></span>
    </p>
  </section>

  <section class="card card--back" aria-label="Business card back">
    <svg class="card__shapes" width="712" height="420" viewBox="0 0 712 420">
      <path d="M245,0 L712,0 L712,420 L248,420 Q384,210 245,0 Z" fill="var(--brand-blue)"
            role="img" aria-label="Blue panel with a subtle geometric pattern"/>
      <path d="M232,0 L245,0 Q375,170 320,320 Q352,160 232,0 Z" fill="var(--brand-gray)"/>
    </svg>

    <div class="brand-vertical">
      <span class="brand-vertical__square"></span>
      <p class="brand-vertical__name">
        <span class="line-main">Quillbrook</span>
        <span class="line-sub">NETWORKS LTD.</span>
      </p>
    </div>

    <div class="contact-block">
      <p class="contact-block__name">Daniel Marsh</p>
      <p class="contact-block__role">Managing Director</p>
      <ul class="contact-list">
        <li>
          <svg viewBox="0 0 24 24" aria-hidden="true"><path d="M3 9c0-3 4-5 9-5s9 2 9 5v2h-5V9H8v2H3zM6 12h12l2 8H4z"/></svg>
          604-555-0148
        </li>
        <li>
          <svg viewBox="0 0 24 24" aria-hidden="true"><path d="M12 2a10 10 0 1 0 0 20 10 10 0 0 0 0-20zm7.9 9h-3.9a15 15 0 0 0-1.4-6.3A8 8 0 0 1 19.9 11zM12 4c.9 1.2 1.8 3.7 2 7h-4c.2-3.3 1.1-5.8 2-7zM9.4 4.7A15 15 0 0 0 8 11H4.1a8 8 0 0 1 5.3-6.3zM4.1 13H8a15 15 0 0 0 1.4 6.3A8 8 0 0 1 4.1 13zM12 20c-.9-1.2-1.8-3.7-2-7h4c-.2 3.3-1.1 5.8-2 7zm2.6-.7A15 15 0 0 0 16 13h3.9a8 8 0 0 1-5.3 6.3z"/></svg>
          www.quillbrook.me
        </li>
        <li>
          <svg viewBox="0 0 24 24" aria-hidden="true"><path d="M2 5h20v14H2zm2 2v.5l8 5.5 8-5.5V7zm0 3v7h16v-7l-8 5.5z"/></svg>
          support@quillbrook.me
        </li>
      </ul>
    </div>
  </section>

</main>
</body>
</html>
```